OpenHarbor Yoga Website Design

Business Logo - attached
5 pages being:
Home
About
Classes
Blog
Contact

Would like Scrolling webpage and yoga symbols to be used.

Must have's being:
Easy to navigate, Text needs to be able to be edited/updated, Enquire Now Links, More Information Links, be a secure site, SEO,

Please refer to attached document for the information for the body of the website.

Target Market(s)

Educators, Community Service, Health and Wellbeing, Mental Health

Industry/Entity Type

Yoga

Coding

Coded - Design and coding required

Number of Pages Required

5+ page

Font styles to use
Other font styles liked:
• Bella Bold BC

Colors
0094D4
00A9DD
6FCCEA
C7EBF8
E9F6FB
6B429C
8869AF
B7A5CE
E3DAEB
F3F0F8

Requirements
Must have
• Easy to navigate, Text needs to be able to be edited/updated, Enquire Now Links, More Information Links, be a secure site, SEO,
Nice to have
• Scrolling webpage, yoga symbols

```html
<!DOCTYPE html>
<html lang="en">
<head>
<meta charset="UTF-8">
<title>OpenHarbor Yoga — Home</title>
<link href="https://fonts.googleapis.com/css2?family=Kaushan+Script&family=Mulish:wght@400;600;700&family=Roboto+Slab:wght@400&display=swap" rel="stylesheet">
<style>
:root{
  --purple:#6B429C;
  --purple-mid:#8869AF;
  --purple-soft:#B7A5CE;
  --purple-pale:#E3DAEB;
  --purple-mist:#F3F0F8;
  --ink:#222222;
  --white:#ffffff;
}
*{margin:0;padding:0;box-sizing:border-box}
html,body{width:1200px;height:2985px;overflow:hidden;background:var(--white)}
body{font-family:'Mulish',sans-serif;color:var(--ink)}
a{text-decoration:none;color:inherit}
.page{position:relative;width:1200px;height:2985px;overflow:hidden}
.script{font-family:'Kaushan Script',cursive;color:var(--purple);font-weight:400}
.rule{position:absolute;height:4px;width:56px;background:var(--purple)}

/* hero */
.hero{position:absolute;left:0;top:0;width:1200px;height:686px;
  background:linear-gradient(180deg,#eef0f1 0%,#e6e7e8 52%,#a89a8e 64%,#6f5e50 80%,#8b7663 88%,#a48d76 100%)}
.hero-figure{position:absolute;left:440px;top:230px;width:330px;height:400px;border-radius:160px 160px 40px 40px;
  background:radial-gradient(ellipse at 50% 45%,rgba(90,80,80,.55),rgba(120,110,110,.15) 70%,transparent 75%)}
.contact-chip{position:absolute;top:38px;display:flex;align-items:center;gap:12px}
.contact-chip .bar{width:2px;height:42px;background:var(--purple)}
.contact-chip .label{font-size:14px;color:var(--ink)}
.contact-chip .value{font-size:18px;color:var(--purple)}
.contact-chip .value.bold{font-weight:700;font-size:19px}
.dots{position:absolute;top:112px;height:8px;
  background-image:radial-gradient(circle,var(--purple) 3.5px,transparent 4px);background-size:25px 8px}
.brand{position:absolute;left:510px;top:62px;width:180px;text-align:center}
.brand .mark{width:16px;height:16px;border-radius:50%;background:var(--purple-mid);margin:0 auto 6px}
.brand .name{font-size:17px;font-weight:600;color:var(--purple)}
.nav a{position:absolute;top:146px;font-size:15px;color:var(--ink);letter-spacing:.3px}
.nav a.active{color:var(--purple);font-weight:700;padding-bottom:8px;border-bottom:3px solid var(--purple)}
.hero-title{position:absolute;left:832px;top:236px;font-size:56px;line-height:88px;white-space:nowrap}
.btn{position:absolute;background:var(--purple);color:var(--white);border-radius:22px;text-align:center}
.btn-enquire{left:834px;top:437px;width:145px;height:40px;line-height:40px;font-family:'Roboto Slab',serif;font-size:18px}

/* welcome */
.welcome-art{position:absolute;left:0;top:720px;width:580px;height:445px;
  background:radial-gradient(circle at 345px 230px,rgba(183,165,206,.55) 0,rgba(227,218,235,.6) 150px,rgba(243,240,248,0) 230px)}
.welcome-art .mark{position:absolute;left:335px;top:150px;width:20px;height:20px;border-radius:50%;background:var(--purple-mid)}
.welcome-art .name{position:absolute;left:225px;top:195px;width:240px;text-align:center;font-size:28px;font-weight:600;color:var(--purple)}
.welcome-head{position:absolute;left:603px;top:727px}
.welcome-head .small{font-size:32px;color:#111;line-height:44px}
.welcome-head .big{font-size:38px;line-height:56px}
.copy-block{position:absolute;font-size:13.9px;line-height:22.5px;text-align:justify}
.copy-block p+p{margin-top:22px}

/* benefits */
.benefits{position:absolute;left:0;top:1165px;width:1200px;height:813px;background:var(--purple-mist)}
.benefits-title{position:absolute;left:0;width:1200px;top:1195px;text-align:center;font-size:42px}
.benefits-intro{position:absolute;left:200px;width:800px;top:1303px;text-align:center;font-size:14.2px;line-height:22.5px}
.btn-benefits{left:513px;top:1372px;width:173px;height:35px;line-height:35px;border-radius:9px;font-size:15px;font-weight:700}
.card{position:absolute;top:1446px;width:292px;height:462px;background:var(--white);border-radius:18px;box-shadow:0 6px 24px rgba(107,66,156,.08)}
.card .icon{width:46px;height:46px;border-radius:50%;background:var(--purple);margin:40px auto 0}
.card h3{margin-top:28px;text-align:center;font-size:16.5px;font-weight:700;letter-spacing:.3px}
.card .line{width:34px;height:3px;background:var(--purple);margin:14px auto 22px}
.card ul{list-style:none;padding:0 20px}
.card li{position:relative;padding:6px 0 6px 34px;font-size:11.8px;line-height:14.5px;border-bottom:1px solid #e2dde8;min-height:32px;display:flex;align-items:center}
.card li:last-child{border-bottom:none}
.card li::before{content:"";position:absolute;left:10px;top:50%;margin-top:-5px;width:10px;height:10px;border-radius:50%;background:var(--purple)}
.silhouette{position:absolute;background:linear-gradient(180deg,var(--purple-mid),var(--purple));opacity:.85}

/* fun */
.fun-title{position:absolute;left:130px;top:2040px;font-size:33px;line-height:52px;white-space:nowrap}
.fun-photo{position:absolute;left:600px;top:2015px;width:600px;height:564px;
  background:radial-gradient(ellipse at 60% 45%,#c9aa93 0,#e8ddd4 35%,rgba(255,255,255,0) 60%),linear-gradient(180deg,#ffffff 0%,#ffffff 70%,#a89078 88%,#7a6552 100%)}

/* footer */
.footer{position:absolute;left:0;top:2579px;width:1200px;height:406px;background:var(--purple);color:var(--white)}
.footer .brand-f{position:absolute;left:120px;top:120px;width:220px;text-align:center}
.footer .brand-f .mark{width:20px;height:20px;border-radius:50%;background:var(--white);margin:0 auto 10px}
.footer .brand-f .name{font-size:22px;font-weight:600}
.footer h4{position:absolute;top:43px;font-family:'Roboto Slab',serif;font-weight:400;font-size:19px;padding-bottom:8px;border-bottom:2px solid var(--white)}
.footer .menu{position:absolute;left:401px;top:103px;list-style:none;font-size:14.6px;line-height:28px}
.footer .row{position:absolute;left:606px;display:flex;gap:16px;align-items:flex-start;font-size:13.4px;line-height:17px}
.footer .row svg{flex:none;margin-top:2px}
.footer .abn{position:absolute;left:614px;top:269px;font-size:14.6px}
.social{position:absolute;top:92px;width:41px;height:41px;border-radius:8px;background:var(--white)}
.social span{position:absolute;inset:8px;border-radius:6px;border:3px solid var(--purple)}
.footer .divider{position:absolute;left:130px;top:316px;width:940px;height:1px;background:rgba(255,255,255,.35)}
.footer .copy{position:absolute;left:0;width:1200px;top:350px;text-align:center;font-size:11.5px}
</style>
</head>
<body>
<div class="page">

  <section class="hero" role="img" aria-label="Photo of a woman seated on a wooden deck with arms raised above her head, hazy mountains behind"></section>
  <div class="hero-figure" aria-hidden="true"></div>

  <div class="contact-chip" style="left:195px">
    <svg width="32" height="24" viewBox="0 0 32 24" fill="none" stroke="#6B429C" stroke-width="1.8"><rect x="9" y="3" width="21" height="17" rx="2"/><path d="M9 5l10.5 8L30 5"/><path d="M1 9h6M3 14h4"/></svg>
    <span class="bar"></span>
    <div><div class="label">Email us:</div><div class="value">hello@openharboryoga.example</div></div>
  </div>
  <div class="contact-chip" style="left:824px">
    <svg width="24" height="24" viewBox="0 0 24 24" fill="none" stroke="#6B429C" stroke-width="1.8"><path d="M5 3l4 1 1 5-2 1a11 11 0 0 0 6 6l1-2 5 1 1 4-3 2C10 21 3 14 3 6z"/><path d="M14 3a7 7 0 0 1 7 7M14 7a3 3 0 0 1 3 3"/></svg>
    <span class="bar"></span>
    <div><div class="label">Phone:</div><div class="value bold">0400 555 218</div></div>
  </div>

  <div class="dots" style="left:190px;width:320px"></div>
  <div class="dots" style="left:675px;width:330px"></div>

  <div class="brand"><div class="mark"></div><div class="name">OpenHarbor Yoga</div></div>

  <nav class="nav">
    <a class="active" href="#" style="left:219px">HOME</a>
    <a href="#" style="left:309px">ABOUT</a>
    <a href="#" style="left:401px">CLASSES</a>
    <a href="#" style="left:777px">BLOG</a>
    <a href="#" style="left:857px">CONTACT</a>
  </nav>

  <h1 class="hero-title script">Open Your<br>Heart Yoga</h1>
  <a class="btn btn-enquire" href="#">Enquire Now</a>

  <div class="welcome-art" role="img" aria-label="Faint yoga pose silhouette behind a large soft brand emblem">
    <span class="mark"></span><span class="name">OpenHarbor Yoga</span>
  </div>
  <div class="welcome-head">
    <div class="small script" style="color:#111">Welcome to</div>
    <div class="big script">OpenHarbor Yoga</div>
  </div>
  <div class="rule" style="left:604px;top:834px"></div>
  <div class="copy-block" style="left:603px;top:868px;width:460px">
    <p>OpenHarbor Yoga believe that you are never too young to benefit from and fall in love with yoga. My aim is to EMPOWER kids and teens to thrive by teaching life skills in Yoga, Mindfulness and Breathing techniques to deal with daily challenges and big emotions.</p>
    <p>OpenHarbor Yoga gives kids an opportunity to enjoy and experience yoga for themselves and primarily focuses on programs for Schools, Pre Schools and Early Learning Centres, Private Classes, Sporting Clubs, Martial Arts Schools, Scout Groups and Occupational Therapy Centres just to name a few. All classes are age appropriate and encourage children’s natural drive to learn, move, and be creative.</p>
  </div>

  <section class="benefits"></section>
  <h2 class="benefits-title script">Benefits of Yoga</h2>
  <div class="rule" style="left:572px;top:1274px"></div>
  <p class="benefits-intro">The benefits of yoga can last a lifetime. It is my aim &amp; passion to introduce yoga to kids of all ages and backgrounds<br>so that they can not only experience the benefits of yoga but fall in love with the practice.</p>
  <div class="btn btn-benefits">Yoga benefits include</div>

  <article class="card" style="left:132px">
    <div class="icon"></div>
    <h3>HEALTHY BODIES</h3><div class="line"></div>
    <ul>
      <li>Develops strong, flexible<br>and healthy bodies</li>
      <li>Promotes spinal alignment<br>and good posture</li>
      <li>Builds energy and stamina</li>
      <li>Improves internal physical function - organs, digestion, elimination, circulation, and blood flow.</li>
      <li>Helps breathing and lung capacity Teaches the enjoyment of movement Works the ‘whole’ body</li>
    </ul>
  </article>
  <article class="card" style="left:453px">
    <div class="icon"></div>
    <h3>HEALTHY MINDS</h3><div class="line"></div>
    <ul>
      <li>Cultivates confidence and<br>self-esteem</li>
      <li>Develops concentration and<br>attention</li>
      <li>Helps relax and sleep better</li>
      <li>Clears the mind for better clarity<br>and decision making</li>
      <li>Calms the nervous system</li>
      <li>Learns to cope with stressful situations</li>
      <li>Balances emotions</li>
    </ul>
  </article>
  <article class="card" style="left:774px">
    <div class="icon"></div>
    <h3>HEALTHY SPIRITS</h3><div class="line"></div>
    <ul>
      <li>Fosters creativity, expression and<br>imagination</li>
      <li>Cultivates kindness to themselves<br>and others</li>
      <li>Cultivates respect for self and others</li>
      <li>Builds balance and inner quiet</li>
      <li>Builds inner strength and resilience</li>
      <li>Teaches self-awareness</li>
      <li>Teaches self-awareness</li>
    </ul>
  </article>

  <div class="silhouette" style="left:0;top:1775px;width:125px;height:203px;border-radius:60px 60px 0 0" role="img" aria-label="Purple silhouette of a yoga warrior pose"></div>
  <div class="silhouette" style="left:1070px;top:1812px;width:130px;height:166px;border-radius:60px 60px 0 0" role="img" aria-label="Purple silhouette of a standing dancer yoga pose"></div>

  <div class="fun-photo" role="img" aria-label="Photo of a woman meditating cross-legged on a wooden deck with eyes closed"></div>
  <h2 class="fun-title script">OpenHarbor Yoga combines all the<br>benefits of traditional yoga<br>and a lot of fun!</h2>
  <div class="rule" style="left:130px;top:2219px"></div>
  <div class="copy-block" style="left:130px;top:2259px;width:481px">
    <p>We play games and practice engaging flows which get our bodies moving, then we take a quiet moment to be still and calm as we focus on our breathing.</p>
    <p>OpenHarbor Yoga Kids will learn that relaxation is just as important as moving their bodies, and the exercises which they learn in class can easily be repeated at any time in their busy day to feel calm and grounded.</p>
  </div>

  <footer class="footer">
    <div class="brand-f"><div class="mark"></div><div class="name">OpenHarbor Yoga</div></div>

    <h4 style="left:401px">Menu</h4>
    <ul class="menu"><li>Home</li><li>About</li><li>Classes</li><li>Blog</li><li>Contact</li></ul>

    <h4 style="left:613px">Contact Us</h4>
    <div class="row" style="top:104px">
    <svg width="20" height="24" viewBox="0 0 20 24" fill="none" stroke="#fff" stroke-width="2"><path d="M10 22s7-7 7-13a7 7 0 0 0-14 0c0 6 7 13 7 13z"/><circle cx="10" cy="9" r="2.5" fill="#fff"/></svg>
    <div>Fernvale,<br>Victoria Australia 3999</div></div>
    <div class="row" style="top:157px">
    <svg width="22" height="22" viewBox="0 0 24 24" fill="none" stroke="#fff" stroke-width="1.8"><path d="M5 3l4 1 1 5-2 1a11 11 0 0 0 6 6l1-2 5 1 1 4-3 2C10 21 3 14 3 6z"/><path d="M14 3a7 7 0 0 1 7 7M14 7a3 3 0 0 1 3 3"/></svg>
    <div>Call Us<br>0400 555 218</div></div>
    <div class="row" style="top:210px;left:600px">
    <svg width="30" height="22" viewBox="0 0 32 24" fill="none" stroke="#fff" stroke-width="1.8"><rect x="9" y="3" width="21" height="17" rx="2"/><path d="M9 5l10.5 8L30 5"/><path d="M1 9h6M3 14h4"/></svg>
    <div>Email Us<br>hello@openharboryoga.example</div></div>
    <div class="abn">ABN:&nbsp; 12 345 678 901</div>

    <h4 style="left:921px">Follow Us</h4>
    <a class="social" href="#" aria-label="Social profile one" style="left:919px"><span></span></a>
    <a class="social" href="#" aria-label="Social profile two" style="left:967px"><span></span></a>

    <div class="divider"></div>
    <div class="copy">Copyright © 2023 All Rights Reserved</div>
  </footer>

</div>
</body>
</html>
```